NimbaVault Website Homepage Design

Please provide your idea of homepage for a hosting company. This project is for DESIGN only, no coding.

It must use/combine colors used in logo, clean, modern look.

Homepage must consist of at least 4 sections (example: testimonials, services, and so on. not necesarily all of them). We would like the navigation to be horizontal, but not mandatory.

You can include a preview of services page (optional, not a must).

Number of Pages Required

1 page

Font styles to use
Sans Serif

```html
<!DOCTYPE html>
<html lang="en">
<head>
<meta charset="utf-8">
<title>NimbaVault — Homepage</title>
<link href="https://fonts.googleapis.com/css2?family=Montserrat:wght@300;400;600;700;800&family=Mulish:ital,wght@0,400;0,600;0,700;1,400&display=swap" rel="stylesheet">
<style>
:root{
  --blue:#0b63ce;
  --blue-bright:#1f7ae0;
  --navy:#1f2536;
  --ink:#1c1c1c;
  --text:#3c3c3c;
  --muted:#6b6f78;
  --light:#f5f6f8;
  --white:#ffffff;
  --star:#f2a100;
}
*{margin:0;padding:0;box-sizing:border-box}
html,body{width:1200px;height:3589px;overflow:hidden}
body{position:relative;background:var(--white);font-family:"Mulish",sans-serif;color:var(--text)}
.abs{position:absolute}
.brand{font-family:"Montserrat",sans-serif;font-weight:800;color:var(--blue);letter-spacing:1px;display:flex;align-items:center;gap:10px}
.brand .dot{width:.8em;height:.8em;border-radius:50%;background:var(--blue)}

/* header */
.site-header{left:0;top:0;width:1200px;height:84px;background:var(--white)}
.site-header .brand{position:absolute;left:114px;top:22px;font-size:34px}
.main-nav{position:absolute;left:422px;top:32px;font-family:"Montserrat",sans-serif;font-weight:600;font-size:15px}
.main-nav a{position:absolute;white-space:nowrap;text-decoration:none;color:#5a5a5a}
.main-nav a.active{color:var(--blue)}
.btn{display:inline-flex;align-items:center;justify-content:center;font-family:"Montserrat",sans-serif;font-weight:700;text-transform:uppercase;text-decoration:none}
.btn-start{position:absolute;left:945px;top:21px;width:130px;height:40px;background:var(--blue);color:var(--white);font-size:13px;border-radius:2px}

/* hero */
.hero{left:0;top:84px;width:1200px;height:692px;background:radial-gradient(ellipse at 65% 40%,#2d5aa0 0%,#132a55 45%,#07142d 100%)}
.hero .brand{position:absolute;left:114px;top:158px;font-size:58px;color:var(--blue-bright)}
.hero h1{position:absolute;left:114px;top:248px;font-family:"Montserrat",sans-serif;font-weight:800;font-size:38px;line-height:46px;color:var(--white)}
.hero p{position:absolute;left:113px;top:348px;font-family:"Montserrat",sans-serif;font-weight:300;font-size:24px;line-height:33px;color:var(--white)}
.domain-search{position:absolute;left:114px;top:434px;width:441px;height:53px;display:flex}
.domain-search .field{flex:1;background:var(--white);border-radius:4px 0 0 4px;padding:0 28px;display:flex;align-items:center;font-size:15px;color:#8a8a8a}
.domain-search .go{width:98px;background:var(--blue);color:var(--white);font-size:15px;border-radius:0 4px 4px 0}
.slider-dots{position:absolute;left:562px;top:614px;display:flex;gap:7px}
.slider-dots span{width:14px;height:14px;border-radius:50%;border:2px solid var(--white)}
.slider-dots span.on{background:var(--white)}

/* section marker */
.marker{width:44px;height:44px;border-radius:50%;background:var(--blue);display:flex;align-items:center;justify-content:center;z-index:3}
.marker-line{width:2px;background:var(--blue)}

.section-title{position:absolute;left:0;width:1200px;text-align:center;font-family:"Montserrat",sans-serif;font-weight:300;color:var(--ink)}
.section-title b{font-weight:800}

/* services */
.service{width:280px;height:344px;background:var(--white);box-shadow:0 3px 14px rgba(0,0,0,.13);text-align:center}
.service .ico{width:106px;height:106px;border-radius:50%;background:var(--blue);margin:40px auto 0;display:flex;align-items:center;justify-content:center}
.service h3{font-family:"Montserrat",sans-serif;font-weight:700;font-size:19px;color:var(--ink);margin-top:20px}
.service p{font-size:15px;line-height:21.6px;color:#444;margin:16px 22px 0}
.service.featured{height:390px;background:linear-gradient(160deg,#1c78e2,#0a5bc4)}
.service.featured .ico{border:2px solid var(--white);margin-top:32px}
.service.featured h3,.service.featured p{color:var(--white)}
.service .more{margin-top:18px;width:134px;height:35px;border:2px solid var(--white);color:var(--white);font-size:12px}

/* welcome */
.welcome{left:0;top:1763px;width:1200px;height:307px;background:var(--light)}
.welcome-text{position:absolute;left:185px;top:1944px;width:830px;text-align:center;font-size:16px;line-height:24px;color:#444}
.server-hall{left:0;top:2070px;width:1200px;height:390px;background:linear-gradient(90deg,#2a2334 0%,#4a3b55 25%,#e9b3b0 48%,#c8d6ec 52%,#4a3b55 75%,#2a2334 100%)}
.btn-learn{position:absolute;left:527px;top:2097px;width:146px;height:40px;background:var(--blue);color:var(--white);font-size:14px}

/* testimonials */
.clients{left:0;top:2460px;width:1200px;height:641px;background:linear-gradient(180deg,#f4f5f8,#fbfbfc 60%,#f1f2f5)}
.quote{width:411px;height:251px;background:var(--white);border-radius:18px;box-shadow:0 4px 16px rgba(0,0,0,.1);padding:42px 24px 0 46px}
.quote .mark{position:absolute;left:46px;top:34px;font-family:Georgia,serif;font-size:56px;line-height:1;color:#d8dbe2}
.quote p{position:relative;font-style:italic;font-size:15px;line-height:22.5px;color:#444}
.quote .stars{position:relative;margin-top:20px;color:var(--star);font-size:17px;letter-spacing:3px}
.quote .tail{position:absolute;right:52px;bottom:-38px;width:0;height:0;border-left:60px solid transparent;border-top:40px solid var(--white)}
.avatar{width:90px;height:90px;border-radius:50%;background:linear-gradient(135deg,#9fb4cf,#3d5a86)}
.person{font-family:"Montserrat",sans-serif;font-weight:700;font-size:12.5px;line-height:22px;color:var(--ink)}
.arrow{width:34px;height:34px;border-radius:50%;background:#5f636b;display:flex;align-items:center;justify-content:center;z-index:4}

/* footer */
.site-footer{left:0;top:3101px;width:1200px;height:488px;background:var(--navy);color:#e6e8ee}
.site-footer .brand{position:absolute;left:118px;top:88px;font-size:29px;color:var(--blue-bright)}
.foot-about{position:absolute;left:118px;top:152px;width:260px;font-size:15.5px;line-height:22.5px}
.socials{position:absolute;left:118px;top:270px;display:flex;gap:4px}
.socials span{width:29px;height:29px;border-radius:50%;border:1.5px solid #e6e8ee}
.foot-title{position:absolute;font-family:"Montserrat",sans-serif;font-weight:300;font-size:23px;color:var(--white);white-space:nowrap}
.foot-title b{font-weight:700}
.news-text{position:absolute;left:407px;top:153px;width:270px;font-size:15.5px;line-height:22.5px}
.news-field{position:absolute;left:407px;top:202px;width:272px;height:38px;background:var(--white);border-radius:20px;padding-left:20px;display:flex;align-items:center;color:#777;font-size:14px}
.btn-sub{position:absolute;left:407px;top:258px;width:137px;height:34px;background:var(--blue);color:var(--white);border-radius:18px;font-size:15px}
.contact-list{position:absolute;left:716px;top:150px;width:240px;list-style:none;font-size:15.5px;line-height:21px}
.contact-list li{display:flex;gap:18px;margin-bottom:16px}
.contact-list svg{flex:none;margin-top:3px}
.quick-links{position:absolute;left:959px;top:145px;list-style:none;font-size:15.5px;line-height:27.5px}
.copyright{position:absolute;left:0;top:431px;width:1200px;text-align:center;font-size:15.5px}
</style>
</head>
<body>

<header class="site-header abs">
  <div class="brand"><span class="dot"></span>NimbaVault</div>
  <nav class="main-nav">
    <a class="active" style="left:0">HOME</a>
    <a style="left:70px">ABOUT</a>
    <a style="left:147px">OUR SERVICES</a>
    <a style="left:279px">TESTIMONIALS</a>
    <a style="left:414px">CONTACT</a>
  </nav>
  <a class="btn btn-start">Get Started</a>
</header>

<section class="hero abs" role="img" aria-label="Engineer holding a laptop in a dark blue data center aisle">
  <div class="brand"><span class="dot"></span>NimbaVault</div>
  <h1>FIND YOUR PERFECT<br>VPS HOSTING</h1>
  <p>Web Hosting, Domain Name and<br>Hosting Center Solutions</p>
  <div class="domain-search"><div class="field">enter your domain here</div><a class="btn go">Search</a></div>
  <div class="slider-dots"><span class="on"></span><span></span><span></span><span></span></div>
</section>

<svg width="0" height="0" style="position:absolute">
  <symbol id="stack" viewBox="0 0 24 24"><g fill="none" stroke="#fff" stroke-width="2"><rect x="3" y="3" width="18" height="5" rx="1"/><rect x="3" y="10" width="18" height="5" rx="1"/><rect x="3" y="17" width="18" height="4" rx="1"/></g></symbol>
</svg>

<div class="abs marker" style="left:578px;top:754px"><svg width="22" height="22"><use href="#stack"/></svg></div>
<div class="abs marker-line" style="left:599px;top:798px;height:45px"></div>

<h2 class="section-title" style="top:862px;font-size:38px">Our <b>Services</b></h2>

<article class="service abs" style="left:144px;top:969px">
  <div class="ico"><svg width="56" height="56" viewBox="0 0 24 24" fill="none" stroke="#fff" stroke-width="1.4"><path d="M7 10a4 4 0 0 1 8-1 3 3 0 0 1 2 6H7a3 3 0 0 1 0-5z"/><rect x="5" y="16" width="9" height="5"/></svg></div>
  <h3>Cloud Hosting</h3>
  <p>Sed ut perspiciatis unde omnis iste natus error sit voluptatem accusantium doloremque laium, totam rem aperiam, eaque ipsa quae ab illo inventore</p>
</article>
<article class="service featured abs" style="left:460px;top:945px">
  <div class="ico"><svg width="56" height="56" viewBox="0 0 24 24" fill="none" stroke="#fff" stroke-width="1.4"><rect x="4" y="3" width="11" height="17"/><path d="M6 7h7M6 10h7"/><circle cx="17" cy="16" r="3.5"/></svg></div>
  <h3>VPS Hosting</h3>
  <p>Sed ut perspiciatis unde omnis iste natus error sit voluptatem accusantium doloremque laium, totam rem aperiam, eaque ipsa quae ab illo inventore</p>
  <a class="btn more">Learn More</a>
</article>
<article class="service abs" style="left:775px;top:969px">
  <div class="ico"><svg width="56" height="56" viewBox="0 0 24 24" fill="none" stroke="#fff" stroke-width="1.4"><ellipse cx="11" cy="5" rx="7" ry="2.5"/><path d="M4 5v9c0 1.4 3 2.5 7 2.5"/><path d="M18 5v5"/><rect x="11" y="12" width="10" height="9"/></svg></div>
  <h3>Dedicated Hosting</h3>
  <p>Sed ut perspiciatis unde omnis iste natus error sit voluptatem accusantium doloremque laium, totam rem aperiam, eaque ipsa quae ab illo inventore</p>
</article>

<article class="service abs" style="left:144px;top:1345px">
  <div class="ico"><svg width="56" height="56" viewBox="0 0 24 24" fill="none" stroke="#fff" stroke-width="1.4"><rect x="3" y="6" width="14" height="10"/><path d="M8 19h4"/><path d="M17 4l4 1.5v3c0 2-2 3.5-4 4-2-.5-4-2-4-4v-3z"/></svg></div>
  <h3>Web Security</h3>
  <p>Sed ut perspiciatis unde omnis iste natus error sit voluptatem accusantium doloremque laium, totam rem aperiam, eaque ipsa quae ab illo inventore</p>
</article>
<article class="service abs" style="left:460px;top:1369px">
  <div class="ico"><svg width="56" height="56" viewBox="0 0 24 24" fill="none" stroke="#fff" stroke-width="1.4"><rect x="3" y="4" width="18" height="13"/><path d="M9 21h6M12 17v4"/><circle cx="12" cy="10.5" r="2.5"/></svg></div>
  <h3>Easy Setup</h3>
  <p>Sed ut perspiciatis unde omnis iste natus error sit voluptatem accusantium doloremque laium, totam rem aperiam, eaque ipsa quae ab illo inventore</p>
</article>
<article class="service abs" style="left:775px;top:1345px">
  <div class="ico"><svg width="56" height="56" viewBox="0 0 24 24" fill="none" stroke="#fff" stroke-width="1.4"><rect x="4" y="3" width="10" height="5"/><rect x="4" y="9" width="10" height="5"/><rect x="4" y="15" width="10" height="5"/><circle cx="16" cy="14" r="4"/><path d="M19 17l2 2"/></svg></div>
  <h3>Backups</h3>
  <p>Sed ut perspiciatis unde omnis iste natus error sit voluptatem accusantium doloremque laium, totam rem aperiam, eaque ipsa quae ab illo inventore</p>
</article>

<section class="welcome abs"></section>
<div class="abs marker" style="left:578px;top:1783px"><svg width="22" height="22"><use href="#stack"/></svg></div>
<div class="abs marker-line" style="left:599px;top:1827px;height:45px"></div>
<h2 class="section-title" style="top:1882px;font-size:40px">Welcome to <b>NimbaVault</b></h2>
<p class="welcome-text">Sed ut perspiciatis unde omnis iste natus error sit voluptatem accusantium doloremque laudantium, totam rem aperiam, eaque ipsa quae ab illo inventore veritatis et quasi architecto beatae vitae dicta sunt explicabo. Nemo enim ipsam voluptatem quia voluptas sit aspernatur aut odit aut fugit, sed quia conntur magni dolores eos qui ratione voluptatem sequi nesciunt. Neque porro quisquam est, qui dolorem ipsum quia dolor sit amet, consectetur, adipisci velit</p>
<div class="server-hall abs" role="img" aria-label="Two rows of server racks receding toward a pink horizon"></div>
<a class="btn btn-learn">Learn More</a>

<section class="clients abs"></section>
<div class="abs marker" style="left:578px;top:2434px"><svg width="22" height="22"><use href="#stack"/></svg></div>
<div class="abs marker-line" style="left:599px;top:2478px;height:45px"></div>
<h2 class="section-title" style="top:2552px;font-size:38px">What <b>Our Clients Say!</b></h2>

<blockquote class="quote abs" style="left:166px;top:2648px">
  <span class="mark">“</span>
  <p>Sed ut perspiciatis unde omnis iste natus error sit voluptatem accntium doloremque launtium, totam rem aperiam, eaque ipsa quae ab illo intore veritatis et quasi architecto beatae vitae dicta sunt explicabo. Nemo enim ipsam votatem quia voluptas sit aspernatur aut odit aut fugit,</p>
  <div class="stars">★★★★★</div>
  <span class="tail"></span>
</blockquote>
<blockquote class="quote abs" style="left:622px;top:2648px">
  <span class="mark">“</span>
  <p>Sed ut perspiciatis unde omnis iste natus error sit voluptatem accntium doloremque launtium, totam rem aperiam, eaque ipsa quae ab illo intore veritatis et quasi architecto beatae vitae dicta sunt explicabo. Nemo enim ipsam votatem quia voluptas sit aspernatur aut odit aut fugit,</p>
  <div class="stars">★★★★★</div>
  <span class="tail"></span>
</blockquote>

<div class="abs arrow" style="left:151px;top:2756px"><svg width="12" height="12" viewBox="0 0 12 12"><path d="M8 2L4 6l4 4" fill="none" stroke="#fff" stroke-width="1.6"/></svg></div>
<div class="abs arrow" style="left:1014px;top:2756px"><svg width="12" height="12" viewBox="0 0 12 12"><path d="M4 2l4 4-4 4" fill="none" stroke="#fff" stroke-width="1.6"/></svg></div>

<div class="abs avatar" style="left:224px;top:2924px" role="img" aria-label="Client portrait"></div>
<div class="abs person" style="left:328px;top:2946px">JOHN DOE<br>NIMBAVAULT</div>
<div class="abs avatar" style="left:670px;top:2924px" role="img" aria-label="Client portrait"></div>
<div class="abs person" style="left:776px;top:2946px">JOHN DOE<br>NIMBAVAULT</div>

<footer class="site-footer abs">
  <div class="brand"><span class="dot"></span>NimbaVault</div>
  <p class="foot-about">Sed ut perspiciatis unde omnis iste natus error sit vtem accusantium dolorque lam, totam rem aperiam, eaque ipsa quae ab illo</p>
  <div class="socials"><span></span><span></span><span></span><span></span></div>

  <h4 class="foot-title" style="left:407px;top:96px"><b>Sign up for</b> newsletter</h4>
  <p class="news-text">excepteur sint occaecat cupidatat non proident, sunt in culpa qui</p>
  <div class="news-field">Enter email</div>
  <a class="btn btn-sub">Subscribe</a>

  <h4 class="foot-title" style="left:716px;top:96px"><b>Contact</b> us</h4>
  <ul class="contact-list">
    <li><svg width="16" height="20" viewBox="0 0 16 20"><path d="M8 1a6 6 0 0 0-6 6c0 5 6 12 6 12s6-7 6-12a6 6 0 0 0-6-6z" fill="#fff"/><circle cx="8" cy="7" r="2.2" fill="#1f2536"/></svg><span>Address.<br>990 enim ipsam<br>voluptatem quia volus</span></li>
    <li><svg width="16" height="16" viewBox="0 0 16 16"><path d="M3 1l3 3-2 2c1 2 3 4 5 5l2-2 3 3-2 3C7 15 1 9 1 3z" fill="#fff"/></svg><span>Phone:<br>555 0142 7788</span></li>
    <li><svg width="16" height="14" viewBox="0 0 16 14"><rect x="0" y="2" width="16" height="11" fill="#fff"/><path d="M0 2l8 6 8-6" fill="none" stroke="#1f2536" stroke-width="1.4"/></svg><span>Email:<br>info@nimbavault.example</span></li>
  </ul>

  <h4 class="foot-title" style="left:955px;top:96px"><b>Quick</b> links</h4>
  <ul class="quick-links">
    <li>Home</li><li>About</li><li>Our Services</li><li>Why Choose Us</li><li>Blog</li><li>Contact</li>
  </ul>

  <p class="copyright">NimbaVault © 2021 All Rights Reserved | Privacy Policy | Terms and Conditions</p>
</footer>
<div class="abs marker" style="left:578px;top:3076px"><svg width="22" height="22"><use href="#stack"/></svg></div>

</body>
</html>
```